Online interactive calendar for training organisation

We have a new website being made and need a design for an online calendar that is interactive and very simple and easy to use. On our main page this calendar will include all of our courses (approx 30 different ones with up to 8 different locations). On our sub pages which have course information, the calendar will only include details of that specific course. Details needed are: Course code, course name/title, date, duration (1/2 day - 5 days), location, price, discount price. Maybe also a key for available or limited spots left? We want a section at the top of the calendar to be able to filter by location or course, and maybe to filter by month also? I have included a spreadsheet with a sample of our courses with this information. Also a sample draft of the main page on our new webpage to show the colour green which is our company colour. Main notes - we want as simple, effective and easy to use as possible.
We will need to know what plug in we can use to get the design you have created.

Target Market(s)

Mining and construction - both companies and individuals

Number of Pages Required

1 page

Colors
cadf82

Requirements
Must have
• Be simple, easy to use, effective.

```html
<!DOCTYPE html>
<html lang="en">
<head>
<meta charset="utf-8">
<title>Groundline Safety – Time Table</title>
<link rel="stylesheet" href="https://fonts.googleapis.com/css2?family=Cabin:wght@400;500;600;700&family=Open+Sans:wght@400;600&display=swap">
<style>
:root{
  --brand-green:#9dc73e;
  --brand-light:#cadf82;
  --course-green:#b5d15c;
  --dark-green:#4d9a1f;
  --price-orange:#f07d0a;
  --text-dark:#222;
  --text-mid:#444;
  --panel-grey:#f2f2f2;
  --card-white:#fff;
  --footer-dark:#2b2b2b;
  --status-available:#3aa62a;
  --status-full:#e0141b;
  --status-wait:#f4c20d;
  --logo-red:#d8231f;
}
*{box-sizing:border-box;margin:0;padding:0}
html,body{width:1200px;height:2300px;overflow:hidden;background:#fff}
body{position:relative;font-family:"Cabin",sans-serif;color:var(--text-dark)}
.abs{position:absolute}

/* top bar */
.top-bar{left:0;top:0;width:1200px;height:31px;background:var(--brand-green)}
.social{display:flex;gap:4px}
.social span{width:16px;height:16px;border-radius:50%;background:#111;display:block}
.top-bar .social{position:absolute;left:227px;top:7px}
.student-btn{position:absolute;left:780px;top:5px;width:88px;height:21px;background:#1b1b1b;color:#fff;font:600 9px "Open Sans",sans-serif;display:flex;align-items:center;justify-content:center;border-radius:2px}
.search-box{position:absolute;left:870px;top:5px;width:106px;height:21px;background:#fff;border-radius:2px}
.search-box svg{position:absolute;right:8px;top:5px}

/* header */
.site-header{left:0;top:31px;width:1200px;height:70px;background:#fff}
.logo{position:absolute;left:228px;top:13px;display:flex;align-items:center;gap:8px}
.logo-mark{width:40px;height:40px;border-radius:50%;background:var(--logo-red)}
.logo-name{font:700 21px "Cabin",sans-serif;color:var(--logo-red);letter-spacing:.5px;line-height:1}
.logo-tag{font:500 9px "Open Sans",sans-serif;color:#333;margin-top:5px;letter-spacing:.4px;padding-left:20px}
.main-nav{position:absolute;right:223px;top:28px;display:flex;gap:17px;font:400 8.5px "Open Sans",sans-serif;color:#333}
.main-nav .active{color:var(--brand-green)}

/* difference section */
.difference{left:0;top:101px;width:1200px;height:535px;background:var(--panel-grey)}
.section-title{position:absolute;width:100%;text-align:center;font:400 29px "Cabin",sans-serif;color:var(--text-dark)}
.difference .section-title{top:44px}
.difference .lede{position:absolute;width:100%;top:84px;text-align:center;font:400 11px "Open Sans",sans-serif;color:#333}
.difference .rule{position:absolute;left:577px;top:111px;width:48px;height:3px;background:var(--brand-light)}
.tile{position:absolute;width:138px}
.tile .photo{width:138px;height:135px}
.tile .label{margin-top:14px;text-align:center;font:400 11.5px "Open Sans",sans-serif;color:#333}

/* timetable */
.timetable-title{top:692px;left:0;width:1200px;text-align:center;font:400 29px "Cabin",sans-serif}
.account-links{left:895px;top:702px;font:600 13px "Cabin",sans-serif;color:#222}
.account-links .register{color:var(--dark-green)}
.filters{left:177px;top:765px;display:flex;align-items:center;font:400 14px "Cabin",sans-serif;color:#222}
.filter-label{margin-right:12px}
.select{width:172px;height:52px;border:2px solid #e3e3e3;display:flex;align-items:center;justify-content:space-between;padding:0 16px;margin-right:21px;font-size:14.5px}
.card-panel{left:87px;top:843px;width:1026px;height:729px;background:var(--panel-grey)}
.course-card{position:absolute;width:440px;height:188px;background:var(--card-white);box-shadow:0 1px 4px rgba(0,0,0,.06);padding:16px 18px 0 18px}
.course-title{font:500 20px/26px "Cabin",sans-serif;color:var(--course-green);text-transform:uppercase;width:370px}
.course-meta{margin-top:6px;font:400 16px "Cabin",sans-serif;color:#333}
.course-meta .sep{margin:0 12px}
.course-meta b{font-weight:700;color:#111}
.course-date{margin-top:12px;font:400 16px "Cabin",sans-serif;color:#333}
.prices{margin-top:14px;font:600 20px "Cabin",sans-serif;padding-left:2px}
.price-now{color:var(--price-orange);margin-right:36px}
.price-was{color:#777;text-decoration:line-through}
.status{position:absolute;right:22px;top:22px;width:8px;height:8px;border-radius:50%}
.available{background:var(--status-available)}
.full{background:var(--status-full)}
.waiting{background:var(--status-wait)}
.legend{left:89px;top:1591px;display:flex;gap:18px;font:400 14px "Cabin",sans-serif;color:#333}
.legend span{display:flex;align-items:center;gap:9px}
.legend i{width:8px;height:8px;border-radius:50%;display:block}

/* banner */
.banner{left:0;top:1677px;width:1200px;height:406px;background:linear-gradient(90deg,#7d7a6c 0%,#a79a6a 30%,#c9c8bf 55%,#e7e7e5 80%,#eeeeed 100%)}
.banner-frame{position:absolute;left:763px;top:65px;width:242px;height:276px;border:14px solid #fff}
.banner-head{position:absolute;left:649px;top:149px;font:700 38px/42px "Cabin",sans-serif;color:#1d1d1d}
.banner-strip{position:absolute;left:650px;top:244px;width:327px;height:24px;background:var(--brand-green);color:#fff;font:400 10px "Open Sans",sans-serif;display:flex;align-items:center;justify-content:center}

/* footer */
.site-footer{left:0;top:2083px;width:1200px;height:176px;background:var(--footer-dark)}
.site-footer .logo{left:226px;top:54px}
.site-footer .logo-mark{width:34px;height:34px}
.follow{position:absolute;left:269px;top:110px;display:flex;align-items:center;gap:8px;font:400 11px "Open Sans",sans-serif;color:#ddd}
.follow .social span{border-radius:2px;background:#111;width:17px;height:17px}
.footer-nav{position:absolute;right:223px;top:71px;display:flex;gap:17px;font:400 8.5px "Open Sans",sans-serif;color:#ddd}
.contact{position:absolute;top:107px;display:flex;align-items:center;gap:12px;font:400 10px "Open Sans",sans-serif;color:#ddd}
.contact .ico{width:22px;height:22px;background:#111;display:flex;align-items:center;justify-content:center}
.to-top{left:1007px;top:2237px;width:37px;height:37px;background:#fff;border:1px solid #ccc;display:flex;align-items:center;justify-content:center}
.copyright{left:0;top:2259px;width:1200px;height:41px;background:var(--brand-green);display:flex;align-items:center;justify-content:center;font:400 9px "Open Sans",sans-serif;color:#333}
</style>
</head>
<body>

<div class="abs top-bar">
  <div class="social"><span></span><span></span><span></span><span></span></div>
  <div class="student-btn">Student Access</div>
  <div class="search-box"><svg width="10" height="10" viewBox="0 0 10 10"><circle cx="4" cy="4" r="3" fill="none" stroke="#111" stroke-width="1.6"/><line x1="6.2" y1="6.2" x2="9" y2="9" stroke="#111" stroke-width="1.8"/></svg></div>
</div>

<header class="abs site-header">
  <div class="logo">
    <div class="logo-mark"></div>
    <div>
      <div class="logo-name">GROUNDLINE SAFETY</div>
      <div class="logo-tag">SAFETY AND TRAINING</div>
    </div>
  </div>
  <nav class="main-nav"><span class="active">Home</span><span>Courses</span><span>Our Services</span><span>About us</span><span>Funding</span><span>Locations</span><span>Contact us</span></nav>
</header>

<section class="abs difference">
  <h2 class="section-title">THE GROUNDLINE SAFETY DIFFERENCE</h2>
  <p class="lede">Committed to helping our students succeed.</p>
  <div class="rule"></div>

  <div class="tile" style="left:226px;top:144px"><div class="photo" role="img" aria-label="Loader working on a mine site" style="background:linear-gradient(135deg,#6b6a64,#b8a46a)"></div><div class="label">All Courses</div></div>
  <div class="tile" style="left:376px;top:144px"><div class="photo" role="img" aria-label="Handshake with work gloves against blue sky" style="background:linear-gradient(135deg,#9ccbec,#d8c77a)"></div><div class="label">Funded courses</div></div>
  <div class="tile" style="left:529px;top:144px"><div class="photo" role="img" aria-label="Red dump truck in a quarry" style="background:linear-gradient(135deg,#8e8c86,#b53a3a)"></div><div class="label">Mining</div></div>
  <div class="tile" style="left:684px;top:144px"><div class="photo" role="img" aria-label="Excavator on rocky ground" style="background:linear-gradient(135deg,#b9c3c7,#6e5f45)"></div><div class="label">Standard 11</div></div>
  <div class="tile" style="left:838px;top:144px"><div class="photo" role="img" aria-label="Workers with harnesses working at height" style="background:linear-gradient(135deg,#c9cdd0,#5a5e62)"></div><div class="label">Work safely at heights</div></div>

  <div class="tile" style="left:226px;top:326px"><div class="photo" role="img" aria-label="Corporate meeting at an office desk" style="background:linear-gradient(135deg,#6d6f72,#cfc9bd)"></div><div class="label">Corporate clients</div></div>
  <div class="tile" style="left:376px;top:326px"><div class="photo" role="img" aria-label="Group of students at a laptop" style="background:linear-gradient(135deg,#d9c9b0,#e2a53a)"></div><div class="label">Online courses</div></div>
  <div class="tile" style="left:529px;top:326px"><div class="photo" role="img" aria-label="Site workers in hard hats reviewing plans" style="background:linear-gradient(135deg,#7fb3e0,#c9c46a)"></div><div class="label">RPL's &amp; VOC's</div></div>
  <div class="tile" style="left:684px;top:326px"><div class="photo" role="img" aria-label="Worker beside a yellow elevated work platform" style="background:linear-gradient(135deg,#9aa6ad,#d9c540)"></div><div class="label">Plant &amp; Equipment</div></div>
  <div class="tile" style="left:838px;top:326px"><div class="photo" role="img" aria-label="Construction worker on a building site" style="background:linear-gradient(135deg,#8a98b0,#c48a4a)"></div><div class="label">Construction</div></div>
</section>

<h2 class="abs timetable-title">TIME TABLE</h2>
<div class="abs account-links">LOG IN &nbsp;/&nbsp; <span class="register">REGISTER</span></div>

<div class="abs filters">
  <span class="filter-label">BY LOCATION</span>
  <div class="select"><span>Ridgeford</span><svg width="8" height="12" viewBox="0 0 8 12"><path d="M4 0L8 5H0z M4 12L0 7h8z" fill="#111"/></svg></div>
  <span class="filter-label">BY COURSE</span>
  <div class="select"><span>Select Course</span><svg width="8" height="12" viewBox="0 0 8 12"><path d="M4 0L8 5H0z M4 12L0 7h8z" fill="#111"/></svg></div>
  <span class="filter-label" style="margin-left:6px">BY MONTH</span>
  <div class="select" style="margin-right:0"><span>Select Month</span><svg width="8" height="12" viewBox="0 0 8 12"><path d="M4 0L8 5H0z M4 12L0 7h8z" fill="#111"/></svg></div>
</div>

<div class="abs card-panel"></div>

<article class="course-card" style="left:104px;top:866px">
  <h3 class="course-title">RIIHAN304D Work Safely at Heights</h3>
  <p class="course-meta">1 day<span class="sep">|</span>8am<span class="sep">|</span><b>Ridgeford</b></p>
  <p class="course-date">Tuesday, October 29, 2019</p>
  <p class="prices"><span class="price-now">$ 500.00</span><span class="price-was">$ 120.00</span></p>
  <i class="status available"></i>
</article>
<article class="course-card" style="left:582px;top:866px">
  <h3 class="course-title" style="width:380px">CPCCCM208 Dogging &amp; TLILIC0005 Front End Loader Bundle</h3>
  <p class="course-meta">10 days<span class="sep">|</span>8am<span class="sep">|</span><b>Ridgeford</b></p>
  <p class="course-date">Monday, October 28, 2019</p>
  <p class="prices"><span class="price-now">$ 2,300.00</span><span class="price-was">$ 1,200.00</span></p>
  <i class="status full" style="top:36px"></i>
</article>
<article class="course-card" style="left:104px;top:1074px">
  <h3 class="course-title" style="width:380px">HLTAID005 Confined Space - Practical Only (Theory Online)</h3>
  <p class="course-meta">1/2 day<span class="sep">|</span>1pm<span class="sep">|</span><b>Ridgeford</b></p>
  <p class="course-date">Thursday, January 30, 2020</p>
  <p class="prices"><span class="price-now">$ 80.00</span></p>
  <i class="status waiting"></i>
</article>
<article class="course-card" style="left:582px;top:1074px">
  <h3 class="course-title">RIIHAN304D Work Safely at Heights</h3>
  <p class="course-meta">1 day<span class="sep">|</span>8am<span class="sep">|</span><b>Ridgeford</b></p>
  <p class="course-date">Tuesday, October 29, 2019</p>
  <p class="prices"><span class="price-now">$ 80.00</span></p>
  <i class="status available"></i>
</article>
<article class="course-card" style="left:104px;top:1281px">
  <h3 class="course-title">HLTAID001 First Aid - Practical Only</h3>
  <p class="course-meta">1/2 day<span class="sep">|</span>1pm<span class="sep">|</span><b>Ridgeford</b></p>
  <p class="course-date">Friday, November 15, 2019</p>
  <p class="prices"><span class="price-now">$ 80.00</span></p>
  <i class="status available"></i>
</article>

<div class="abs legend">
  <span><i class="available"></i>Available</span>
  <span><i class="full"></i>Full</span>
  <span><i class="waiting"></i>Waiting list</span>
</div>

<section class="abs banner" role="img" aria-label="Large yellow haul truck on a mine site">
  <div class="banner-frame"></div>
  <h2 class="banner-head">Training a Safety<br>Culture that Counts</h2>
  <div class="banner-strip">NOW TRAINING - Working at Heights &amp; Confined Spaces courses</div>
</section>

<footer class="abs site-footer">
  <div class="logo">
    <div class="logo-mark"></div>
    <div class="logo-name">GROUNDLINE SAFETY</div>
  </div>
  <div class="follow">Follow us on : - <div class="social"><span></span><span></span><span></span><span></span></div></div>
  <nav class="footer-nav"><span>Home</span><span>Courses</span><span>Our Services</span><span>About us</span><span>Funding</span><span>Locations</span><span>Contact us</span></nav>
  <div class="contact" style="left:588px">
    <span class="ico"><svg width="9" height="12" viewBox="0 0 9 12"><path d="M4.5 0A4.5 4.5 0 0 0 0 4.5C0 8 4.5 12 4.5 12S9 8 9 4.5A4.5 4.5 0 0 0 4.5 0z" fill="#fff"/><circle cx="4.5" cy="4.5" r="1.6" fill="#111"/></svg></span>
    18 Foundry Lane, Ridgeford QLD 4300
  </div>
  <div class="contact" style="left:826px">
    <span class="ico"><svg width="12" height="9" viewBox="0 0 12 9"><rect width="12" height="9" fill="#fff"/><path d="M0 0l6 5 6-5" fill="none" stroke="#111" stroke-width="1.2"/></svg></span>
    info@groundlinesafety.edu.au
  </div>
</footer>

<div class="abs to-top"><svg width="12" height="8" viewBox="0 0 12 8"><path d="M1 7l5-5 5 5" fill="none" stroke="#222" stroke-width="1.8"/></svg></div>
<div class="abs copyright">© Copyright All Right Reserved | Powered by Groundline Safety.</div>

</body>
</html>
```